real esate business card with company logo and name

we need a business card design for a real esate company

The company name is Walsh & Brand Pty Ltd, and we have our logo designed and will upload. We want classic or moden feel. Black or white background. looks more textured. Should include folowinginformations
Owen Walsh and Lucy Brand
Sales Agents & Onsite Manager
p: 07 5948 2063
F: 07 5948 2174
M:0431 857 219
3/42 Marlow Crescent, FERNLEA QLD 4213

We want this business card looks professonal. Thank you in advance.

Industry/Entity Type

Real Estate Agent

Contact Information for Business Card

Owen Walsh and Lucy Brand
Onsite Manager & Sales Agents
p: 07 5948 2063
M:0431 857 219

Font styles to use
Serif

Colors
000000
fbfbfb
333333
959595

Requirements
Must have
• company logo and name, black or white back ground

```html
<!DOCTYPE html>
<html lang="en">
<head>
<meta charset="utf-8">
<title>Walsh &amp; Brand Pty Ltd — Business Card</title>
<link href="https://fonts.googleapis.com/css2?family=Ubuntu:wght@400;500&display=swap" rel="stylesheet">
<style>
  :root {
    --page-bg: #cfcfcf;
    --frost-light: #fbfbfb;
    --frost-mid: #e6e6e6;
    --band-dark: #000000;
    --band-mid: #333333;
    --silver: #959595;
    --silver-bright: #f2f2f2;
    --text-light: #e4e4e4;
    --text-soft: #bdbdbd;
    --rose: #c9a49a;
    --name-light: #dfd3ce;
    --brand-grey: #333333;
  }
  * { margin: 0; padding: 0; box-sizing: border-box; }
  html, body { width: 1200px; height: 969px; overflow: hidden; }
  body {
    background: var(--page-bg);
    font-family: "Ubuntu", sans-serif;
    position: relative;
  }
  .business-card {
    position: absolute;
    left: 80px;
    top: 191px;
    width: 1040px;
    height: 587px;
    overflow: hidden;
    box-shadow: 0 18px 40px rgba(0,0,0,0.25);
  }
  .card-surface { position: absolute; inset: 0; width: 100%; height: 100%; }

  .brand {
    position: absolute;
    left: 104px;
    top: 300px;
    display: flex;
    align-items: center;
    gap: 14px;
  }
  .brand-square {
    width: 26px;
    height: 26px;
    background: var(--brand-grey);
  }
  .brand-name {
    font-weight: 500;
    font-size: 22px;
    letter-spacing: 2px;
    color: var(--brand-grey);
    text-transform: uppercase;
  }

  .address {
    position: absolute;
    right: 52px;
    top: 328px;
    text-align: right;
    font-size: 24px;
    line-height: 33px;
    color: var(--text-light);
  }

  .contact-list {
    position: absolute;
    right: 52px;
    top: 412px;
    list-style: none;
    text-align: right;
  }
  .contact-item {
    display: flex;
    justify-content: flex-end;
    align-items: center;
    gap: 14px;
    font-size: 24px;
    height: 38px;
    color: var(--text-light);
  }
  .contact-item.web { color: var(--text-soft); margin-top: 4px; }
  .contact-icon { width: 24px; height: 24px; fill: #d4d4d4; }

  .people {
    position: absolute;
    left: 57px;
    top: 494px;
  }
  .people-names {
    font-size: 30px;
    color: var(--name-light);
    line-height: 38px;
  }
  .people-names .second, .amp { color: var(--rose); }
  .people-role {
    font-size: 24px;
    color: var(--text-light);
    line-height: 34px;
  }
</style>
</head>
<body>
  <section class="business-card" aria-label="Walsh &amp; Brand Pty Ltd business card">
    <svg class="card-surface" viewBox="0 0 1040 587" preserveAspectRatio="none" aria-hidden="true">
      <defs>
        <linearGradient id="frost" x1="0" y1="0" x2="1" y2="1">
          <stop offset="0" stop-color="#fbfbfb"/>
          <stop offset="0.6" stop-color="#ececec"/>
          <stop offset="1" stop-color="#dcdcdc"/>
        </linearGradient>
        <linearGradient id="band" x1="0" y1="0" x2="1" y2="1">
          <stop offset="0" stop-color="#333333"/>
          <stop offset="0.5" stop-color="#1c1c1c"/>
          <stop offset="1" stop-color="#000000"/>
        </linearGradient>
      </defs>
      <rect class="frost-area" width="1040" height="587" fill="url(#frost)"/>
      <polygon class="bevel-strip" points="0,296 217,458 1040,60 1040,79 217,476 0,314" fill="#959595"/>
      <polyline class="bevel-highlight" points="0,296 217,458 1040,60" fill="none" stroke="#f2f2f2" stroke-width="3"/>
      <polygon class="dark-band" points="0,314 217,476 1040,79 1040,587 0,587" fill="url(#band)"/>
      <polyline class="band-edge" points="0,314 217,476 1040,79" fill="none" stroke="#bdbdbd" stroke-width="1.5"/>
    </svg>

    <div class="brand">
      <span class="brand-square"></span>
      <span class="brand-name">Walsh &amp; Brand Pty Ltd.</span>
    </div>

    <address class="address">
      3/42 Marlow Crescent<br>
      FERNLEA QLD 4213
    </address>

    <ul class="contact-list">
      <li class="contact-item">07 5948 2063
        <svg class="contact-icon" viewBox="0 0 24 24" aria-label="phone"><path d="M6.6 2.5l3 3.2-1.8 2.6c1.3 2.8 3.4 5 6.2 6.4l2.6-1.8 3.2 3-1.6 3.6C10 19.200 4.600 13.800 3 5.200z"/></svg>
      </li>
      <li class="contact-item">0431 857 219
        <svg class="contact-icon" viewBox="0 0 24 24" aria-label="mobile"><path d="M7 1h10a2 2 0 0 1 2 2v18a2 2 0 0 1-2 2H7a2 2 0 0 1-2-2V3a2 2 0 0 1 2-2zm0 3v14h10V4zm5 15.5a1.2 1.2 0 1 0 0 2.4 1.2 1.2 0 0 0 0-2.4z"/></svg>
      </li>
      <li class="contact-item">07 5948 2174
        <svg class="contact-icon" viewBox="0 0 24 24" aria-label="fax"><path d="M6 2h10l2 2v5H6zM3 10h18a2 2 0 0 1 2 2v8H1v-8a2 2 0 0 1 2-2zm3 6v6h12v-6z"/></svg>
      </li>
      <li class="contact-item web">www.walshbrand.com.au
        <svg class="contact-icon" viewBox="0 0 24 24" aria-label="website"><path d="M12 1a11 11 0 1 0 0 22 11 11 0 0 0 0-22zm0 2c1.6 1.4 2.6 4.800 2.800 8H9.200C9.400 7.800 10.400 4.400 12 3zM3.100 11a9 9 0 0 1 4.700-7C7 6 7.200 8.600 7.200 11zm0 2h4.100c.1 2.600.8 5 1.700 7A9 9 0 0 1 3.100 13zM12 21c-1.600-1.400-2.600-4.800-2.800-8h5.600c-.2 3.200-1.200 6.600-2.800 8zm4.200-10c0-2.400-.2-5-1-7a9 9 0 0 1 5.700 7zm-1 9c.9-2 1.600-4.400 1.700-7h4a9 9 0 0 1-5.700 7z"/></svg>
      </li>
    </ul>

    <div class="people">
      <p class="people-names">Owen Walsh <span class="second">&amp; Lucy Brand</span></p>
      <p class="people-role">Sales Agents <span class="amp">&amp;</span> Onsite Manager</p>
    </div>
  </section>
</body>
</html>
```